Spanish Student Needs a Cover for his PhD Dissertation

Hi everyone :) So, I'm a Corneal surgeon currently finishing my PhD, with a dissertation focused on the evaluation of quality of life in patients affected by a disease called Keratoconus. Just so you know, Keratoconus is a condition in which the cornea (the frontal part of the way) gets thin and bulgy and it decreases vision. What I did during my PhD was designing a questionnaire for evaluating quality of life in this kind of patients.
I need to design a hard cover for my dissertation, which is 200 sheets long. I like kind of minimalistic and geometric designs but I am totally open to suggestions. What needs to be in the cover is the name of the dissertation "Diseño, desarrollo y validación de una encuesta para evaluar el compromiso visual y emocional subjetivos en pacientes con Queratocono" and my name, "Iker Zurmendi". The other thing that needs to go there is the logo of my university (Universidad de Montehierro). Aside from that, anything else is up to the designer. It would be important to use the kind of "red" color I am using in the dissertation. I am attaching the frontal page of my dissertation so you know what kind of design and colors I am using.
In the back part, of the cover, there should be this small inscription: "Iker Zurmendi, MD, es un Oftalmólogo Subespecialista en Cirugía Refractiva de la Universidad Tecnológica Cordillerana (Colombia) y la Universidad de Montehierro (España). Actualmente se desempeña como miembro del Departamento de Córnea y Cirugía Refractiva de la Clínica de Oftalmología Miraluz y como director de su propia compañía de emprendimiento médico Silver Heron Surgical". Please leave a space to place my picture; I will have it taken this week so I don't have it right now, you can just leave the blank spot and I will include it later
The size of the pages is standard "letter" size.
Thanks a lot!

Target Market(s)

PhD Scholars

Font styles to use
Serif

Requirements
Must have
• The "red" color I use on my font. It must be formal but "young".
Nice to have
• I like to keep the design clean, kind of "formal with a young" touch so to speak. I really like gray colors, so it would be nice to have broad areas of gray. I love geometrical designs.
I have uploaded a very early version a friend of mine made (it even had a different title); this can be a starting point for you to work on, but I am more than open to suggestions and new ideas.
Should not have
• Please don't use my whole name, Iker Zurmendi is fine. I don't like ALL CAPITALS.

```html
<!DOCTYPE html>
<html lang="es">
<head>
<meta charset="utf-8">
<title>Cubierta de tesis doctoral – Iker Zurmendi</title>
<link rel="stylesheet" href="https://fonts.googleapis.com/css2?family=Libre+Baskerville:wght@400;700&family=Open+Sans:wght@400;600;700&display=swap">
<style>
  :root {
    --wine: #a51f36;
    --wine-deep: #861829;
    --ink: #1f1f21;
    --paper: #ffffff;
    --mist: #d9d9db;
    --stage: #e4e4e6;
    --eye-warm: #b98a6c;
    --eye-cool: #5d7f92;
  }
  * { box-sizing: border-box; margin: 0; padding: 0; }
  html, body { width: 1200px; height: 847px; overflow: hidden; }
  body {
    background: var(--stage);
    display: flex; align-items: center; justify-content: center;
    font-family: "Open Sans", Arial, sans-serif;
  }
  .spread { display: flex; width: 1120px; height: 724px; box-shadow: 0 10px 30px rgba(0,0,0,.18); }
  .panel { position: relative; width: 560px; height: 724px; overflow: hidden; }

  /* Back cover */
  .back {
    background: linear-gradient(160deg, var(--wine) 0%, var(--wine) 55%, var(--wine-deep) 100%);
    color: var(--paper); text-align: center;
  }
  .portrait-slot {
    position: absolute; left: 210px; top: 96px; width: 140px; height: 140px;
    background: linear-gradient(135deg, #f4f4f4, var(--mist));
    display: flex; align-items: center; justify-content: center;
    color: #b5b5b8; font-size: 20px; letter-spacing: 1px;
  }
  .bio {
    position: absolute; left: 60px; right: 60px; top: 300px;
    font-size: 14.5px; line-height: 1.38;
  }
  .bio strong { font-weight: 700; }
  .credits { position: absolute; left: 40px; right: 40px; top: 470px; font-size: 15px; line-height: 1.35; }
  .credits .role { font-weight: 700; font-size: 15px; }

  /* Front cover */
  .front { background: var(--wine); }
  .front svg.geometry { position: absolute; inset: 0; }
  .masthead { position: absolute; top: 26px; left: 180px; right: 20px; text-align: center; }
  .marks { display: flex; justify-content: center; gap: 34px; align-items: center; margin-bottom: 12px; }
  .mark { display: flex; align-items: center; gap: 6px; font-family: "Libre Baskerville", Georgia, serif;
          font-size: 9.5px; font-weight: 700; color: var(--wine); }
  .mark .dot { width: 16px; height: 16px; border-radius: 50%; background: var(--wine); }
  .mark .sq { width: 14px; height: 14px; background: var(--wine); }
  .masthead p { font-family: "Libre Baskerville", Georgia, serif; font-size: 9.5px; line-height: 1.35; color: var(--wine); font-weight: 700; }
  .masthead p.programme { color: var(--ink); font-weight: 400; }
  .title {
    position: absolute; left: 92px; top: 486px; width: 330px;
    font-family: "Libre Baskerville", Georgia, serif; font-weight: 700;
    font-size: 16px; line-height: 1.2; color: var(--paper);
  }
  .author {
    position: absolute; left: 78px; top: 652px; padding-left: 14px;
    border-left: 2px solid var(--paper);
    font-family: "Libre Baskerville", Georgia, serif; font-size: 26px; color: var(--paper);
    line-height: 1.3;
  }
</style>
</head>
<body>
<main class="spread">
  <section class="panel back">
    <div class="portrait-slot">IMAGE</div>
    <p class="bio"><strong>Iker Zurmendi, MD,</strong> es un Oftalmólogo Subespecialista en Cirugía Refractiva de la Universidad Tecnológica Cordillerana (Colombia) y la Universidad de Montehierro (España). Actualmente se desempeña como miembro del Departamento de Córnea y Cirugía Refractiva de la Clínica de Oftalmología Miraluz y como director de su propia compañía de emprendimiento médico Silver Heron Surgical".</p>
    <div class="credits">
      <p class="role">DIRECTOR:</p>
      <p>Dr. Andrés Felipe Olaizola Ruiz</p>
      <p class="role">TUTOR:</p>
      <p>Dr. Luis Ignacio Berrocal Santamaría</p>
    </div>
  </section>

  <section class="panel front">
    <svg class="geometry" width="560" height="724" viewBox="0 0 560 724">
      <defs>
        <linearGradient id="paperGlow" x1="1" y1="0" x2="0" y2="1">
          <stop offset="0" stop-color="#ffffff"/>
          <stop offset="1" stop-color="#d4d4d6"/>
        </linearGradient>
        <linearGradient id="eyeTone" x1="0" y1="0" x2="1" y2="1">
          <stop offset="0" stop-color="#6f6a68"/>
          <stop offset=".45" stop-color="var(--eye-cool)"/>
          <stop offset="1" stop-color="var(--eye-warm)"/>
        </linearGradient>
      </defs>
      <polygon points="30,0 560,0 560,452 120,470" fill="url(#paperGlow)"/>
      <polygon points="232,120 545,415 118,470" fill="url(#eyeTone)" role="img" aria-label="Fotografía de un ojo en primer plano"/>
      <polygon points="228,108 318,108 262,162" fill="var(--ink)"/>
      <polygon points="390,468 560,448 560,640" fill="var(--ink)"/>
      <polygon points="455,470 525,464 495,528" fill="var(--paper)"/>
    </svg>

    <header class="masthead">
      <div class="marks">
        <span class="mark"><span class="dot"></span>Universidad de Montehierro</span>
        <span class="mark"><span class="sq"></span>Escuela de Doctorado Montehierro</span>
      </div>
      <p>Universidad de Montehierro</p>
      <p>Instituto Universitario de Ciencias Oculares Aplicadas</p>
      <p class="programme">Programa de Doctorado en Ciencias de la Visión</p>
    </header>

    <h1 class="title">Diseño, Desarrollo Y Validación De Una Encuesta Para Evaluar El Compromiso Visual Y Emocional Subjetivos En Pacientes Con Queratocono</h1>
    <p class="author">Iker Zurmendi</p>
  </section>
</main>
</body>
</html>
```